Brell Stone Company Business Cards

Front and Back Business Card - logo and text setup - cool design. I need workable photoshop or illustrator files so I can setup each employee card with design that is created
Updates

Hi everyone, thank you for the great entries. Please no more white and blue cards - there are so many already - black and silver only now please. thanks!

Target Market(s)

Construction Industry - Facility Managers

Industry/Entity Type

Construction

Contact Information for Business Card

I really like contemporary simplistic looks - clean neat....not opposed to seeing some black backrounds

Requirements
Must have
• Logo/website address with design on front only - www.brellstone-example.com (logo attached)
• Back:
• Name/Title/Company Address/Phone/email address
Nice to have
• Cool design
Should not have
• Nothing gimmicky like Fire or Water - since we are a Fire Protection company - it has all been done

```html
<!DOCTYPE html>
<html lang="en">
<head>
<meta charset="utf-8">
<title>Brell Stone Company Business Cards</title>
<link href="https://fonts.googleapis.com/css2?family=Lato:wght@400;700;900&display=swap" rel="stylesheet">
<style>
  :root {
    --backdrop: #161616;
    --card: #252525;
    --white: #ffffff;
    --soft: #e6e6e6;
    --accent: #e63b2e;
    --rule: #bdbdbd;
  }
  html, body {
    margin: 0;
    padding: 0;
    width: 1200px;
    height: 912px;
    overflow: hidden;
    background: var(--backdrop);
    font-family: "Lato", Arial, sans-serif;
  }
  .canvas {
    position: relative;
    width: 1200px;
    height: 912px;
  }
  .card {
    position: absolute;
    width: 560px;
    height: 320px;
    background: var(--card);
    box-shadow: 0 18px 40px rgba(0,0,0,0.55);
    box-sizing: border-box;
  }
  .card-front { left: 60px; top: 110px; }
  .card-back { left: 580px; top: 480px; }

  .wordmark {
    display: flex;
    align-items: center;
    gap: 12px;
    color: var(--white);
    font-weight: 900;
    line-height: 1;
    letter-spacing: -1px;
  }
  .wordmark-square {
    width: 18px;
    height: 18px;
    background: var(--accent);
    flex: none;
  }
  .card-front .wordmark {
    position: absolute;
    left: 0; right: 0;
    top: 118px;
    justify-content: center;
    font-size: 56px;
  }
  .front-url {
    position: absolute;
    left: 0; right: 0;
    bottom: 58px;
    text-align: center;
    color: var(--soft);
    font-size: 17px;
    letter-spacing: 0.5px;
  }

  .card-back .wordmark {
    position: absolute;
    left: 34px;
    top: 200px;
    font-size: 38px;
  }
  .back-divider {
    position: absolute;
    left: 300px;
    top: 50px;
    width: 1px;
    height: 220px;
    background: var(--rule);
  }
  .contact {
    position: absolute;
    left: 322px;
    top: 56px;
    color: var(--soft);
    font-size: 13px;
    line-height: 1.35;
  }
  .contact-name {
    color: var(--white);
    font-weight: 700;
    font-size: 20px;
    margin: 0;
  }
  .contact-title {
    color: var(--accent);
    font-size: 14px;
    margin: 2px 0 16px;
  }
  .contact-address { margin: 0 0 14px; }
  .contact-list { list-style: none; margin: 0; padding: 0; }
  .contact-list li {
    display: flex;
    align-items: center;
    gap: 8px;
    margin-bottom: 3px;
  }
  .contact-list svg { width: 12px; height: 12px; flex: none; }
</style>
</head>
<body>
<main class="canvas">

  <section class="card card-front" aria-label="Card front">
    <div class="wordmark"><span class="wordmark-square"></span>Brell Stone</div>
    <div class="front-url">www.brellstone-example.com</div>
  </section>

  <section class="card card-back" aria-label="Card back">
    <div class="wordmark"><span class="wordmark-square"></span>Brell Stone</div>
    <div class="back-divider"></div>
    <div class="contact">
      <p class="contact-name">Dana Hollis Mercer</p>
      <p class="contact-title">President</p>
      <p class="contact-address">48 Harbor Park Lane<br>Millbrook, NY 10990</p>
      <ul class="contact-list">
        <li>
          <svg viewBox="0 0 12 12" aria-hidden="true"><path fill="#e63b2e" d="M2.3 1 L4.3 1 L5 3.6 L3.8 4.6 C4.5 6 5.9 7.4 7.4 8.2 L8.4 7 L11 7.7 L11 9.7 C11 10.4 10.4 11 9.7 11 C5 11 1 7 1 2.3 C1 1.6 1.6 1 2.3 1 Z"/></svg>
          (555) 014-2290
        </li>
        <li>
          <svg viewBox="0 0 12 12" aria-hidden="true"><rect x="0.5" y="2" width="11" height="8" fill="#e63b2e"/><path d="M0.5 2 L6 6.5 L11.5 2" fill="none" stroke="#252525" stroke-width="1"/></svg>
          info@brellstone-example.com
        </li>
        <li>
          <svg viewBox="0 0 12 12" aria-hidden="true"><circle cx="6" cy="6" r="5.2" fill="#e63b2e"/><path d="M0.8 6 H11.2 M6 0.8 V11.2 M6 0.8 C3.5 3.5 3.5 8.5 6 11.2 M6 0.8 C8.5 3.5 8.5 8.5 6 11.2" fill="none" stroke="#252525" stroke-width="0.7"/></svg>
          www.brellstone-example.com
        </li>
      </ul>
    </div>
  </section>

</main>
</body>
</html>
```